Velk Partners Building Business Cards

We need a business card that reflects our business as "Solar Experts" in San Diego. Browse our website www.velkpartners.example our License needs to be displayed as "CSLB# 3867140" our phone number is (619) 555-0187

Save thousands on your electric bills and increase the value of your home while helping to protect the environment. Our solar installation experts will help you design the system that's right for you, using only the highest quality equipment that will look great and give you ideal performance. Our goal is to make you energy independent, and get your electric bill to 0.

Paul Osterby
(619) 555-0187
paul@velkpartners.example

Target Market(s)

Home owners in san diego looking for solar

Industry/Entity Type

Solar Energy

Contact Information for Business Card

Paul Osterby
(619) 555-0187
paul@velkpartners.example

Font styles to use
Other font styles liked:
• Use our logo font

Requirements
Must have
• License needs to be displayed as "CSLB# 3867140" our phone number is (619) 555-0187
Nice to have
• Real images of rooftop home solar in san diego
Should not have
• our business address

```html
<!DOCTYPE html>
<html lang="en">
<head>
<meta charset="utf-8">
<title>Velk Partners Building – Business Card</title>
<link rel="stylesheet" href="https://fonts.googleapis.com/css2?family=Open+Sans:wght@400;700;800&display=swap">
<style>
  :root {
    --navy: #1d3f82;
    --gold: #f2b01e;
    --white: #ffffff;
    --ink: #4a4a4a;
    --page: #e9e7e2;
  }
  * { box-sizing: border-box; margin: 0; padding: 0; }
  html, body { width: 1200px; height: 950px; overflow: hidden; }
  body {
    background: var(--page);
    font-family: "Open Sans", Arial, sans-serif;
    display: flex;
    flex-direction: column;
    align-items: center;
    justify-content: center;
    gap: 50px;
  }
  .card {
    width: 700px;
    height: 400px;
    position: relative;
    overflow: hidden;
    box-shadow: 0 6px 18px rgba(0,0,0,0.18);
  }
  /* Front */
  .card--front { background: var(--white); }
  .front__band {
    height: 92px;
    background: var(--navy);
    padding: 18px 40px 0;
    text-align: right;
  }
  .front__name {
    color: var(--gold);
    font-weight: 700;
    font-size: 24px;
    line-height: 1.2;
  }
  .front__role {
    color: var(--white);
    font-size: 16px;
    line-height: 1.4;
  }
  .front__body {
    padding: 42px 40px 0;
    display: flex;
    flex-direction: column;
    align-items: center;
  }
  .brand {
    display: flex;
    align-items: center;
    gap: 12px;
  }
  .brand__mark {
    width: 26px; height: 26px;
    border-radius: 50%;
    background: var(--gold);
    flex: none;
  }
  .brand__name {
    font-weight: 800;
    font-size: 38px;
    letter-spacing: -0.5px;
    line-height: 1;
  }
  .card--front .brand__name { color: var(--navy); }
  .contact {
    margin-top: 38px;
    text-align: center;
    color: var(--ink);
    font-size: 17px;
    line-height: 1.65;
  }
  .contact__sep { margin: 0 8px; }
  .front__stripe {
    position: absolute;
    left: 0; right: 0; bottom: 0;
    height: 14px;
    background: var(--gold);
  }
  /* Back */
  .card--back {
    background: var(--navy);
    display: flex;
    align-items: center;
    justify-content: center;
  }
  .card--back .brand__name { color: var(--white); font-size: 50px; }
  .card--back .brand__mark { width: 34px; height: 34px; }
</style>
</head>
<body>
  <section class="card card--front" aria-label="Business card front">
    <header class="front__band">
      <p class="front__name">Paul Osterby</p>
      <p class="front__role">CEO/Founder</p>
    </header>
    <div class="front__body">
      <div class="brand">
        <span class="brand__name">Velk Partners Building</span>
        <span class="brand__mark"></span>
      </div>
      <div class="contact">
        <p>CSLB# 3867140</p>
        <p>(619) 555-0187<span class="contact__sep">|</span>paul@velkpartners.example</p>
        <p>www.velkpartners.example</p>
      </div>
    </div>
    <div class="front__stripe"></div>
  </section>

  <section class="card card--back" aria-label="Business card back">
    <div class="brand">
      <span class="brand__name">Velk Partners Building</span>
      <span class="brand__mark"></span>
    </div>
  </section>
</body>
</html>
```